Wordpress theme website for professionals working together

My partner and I are offering business services, my wife in the energy business as mainly as member of the board of commissioners. I am working as interim manager/consultant in the accounting and finance area. Both activities are connected in one company VELMOT BV (dutch ltd). We need a CV based website. Beside this we do some financial and accounting services.

Target Market(s)

small medium business

Font styles to use
Sans Serif

Colors

Designer to choose colors to be used in the design.

Requirements
Must have
• Pictures of both members.
• CLEAN AND SIMPLE
• I LIKE BLACK & WHITE
Nice to have
• I like design like this theme: http://theme.pruxelo-example.com/resume/

```html
<!DOCTYPE html>
<html lang="en">
<head>
<meta charset="utf-8">
<title>VELMOT BV – Maarten</title>
<link href="https://fonts.googleapis.com/css2?family=Montserrat:wght@400;500;600;700&family=Roboto:wght@400;500&display=swap" rel="stylesheet">
<style>
:root{
  --ink:#111111;
  --text:#333333;
  --muted:#7a7a7a;
  --line:#d6d6d6;
  --white:#ffffff;
  --paper:#efefef;
  --hero-a:#d9e0e6;
  --hero-b:#c6d0d8;
  --track:#dcdcdc;
}
*{box-sizing:border-box;margin:0;padding:0}
html,body{width:1200px;height:2688px;overflow:hidden}
body{position:relative;background:var(--white);font-family:"Roboto",Arial,sans-serif;color:var(--text)}
h2.section-title{position:absolute;left:0;width:1200px;text-align:center;font-family:"Montserrat",Arial,sans-serif;font-weight:600;font-size:30px;color:var(--ink)}

/* Hero */
.hero{position:absolute;left:0;top:0;width:1200px;height:540px;background:linear-gradient(100deg,var(--hero-a) 0%,var(--hero-b) 100%);overflow:hidden}
.hero-photo{position:absolute;left:620px;top:0;width:580px;height:540px;background:radial-gradient(ellipse at 55% 45%,#9a8a80 0%,#6f6a68 35%,#3d4348 70%,#2c3238 100%)}
.brand{position:absolute;left:112px;top:30px;font-family:"Montserrat",Arial,sans-serif;font-weight:500;font-size:40px;letter-spacing:1px;color:var(--ink)}
.person-switch{position:absolute;left:660px;top:14px;display:flex;background:var(--white);border-radius:26px}
.person-switch span{display:block;width:146px;height:46px;line-height:46px;text-align:center;font-family:"Montserrat",Arial,sans-serif;font-weight:600;font-size:17px;border-radius:26px}
.person-switch .off{background:var(--white);color:var(--ink)}
.person-switch .on{background:var(--ink);color:var(--white)}
.toolbar{position:absolute;left:1004px;top:24px;display:flex;align-items:center;gap:8px}
.toolbar .dot{width:18px;height:18px;border-radius:50%;background:var(--ink)}
.name-label{position:absolute;left:112px;top:96px;font-size:14px;color:var(--text)}
.name{position:absolute;left:112px;top:112px;font-family:"Montserrat",Arial,sans-serif;font-weight:600;font-size:46px;line-height:1;color:var(--ink)}
.jobs{position:absolute;top:174px;width:220px}
.jobs h4{font-weight:400;font-size:13px;color:var(--text);margin-bottom:14px}
.jobs .job{margin-bottom:20px}
.jobs .job b{display:block;font-family:"Montserrat",Arial,sans-serif;font-weight:600;font-size:15px;color:var(--ink)}
.jobs .job small{display:block;font-size:12px;color:var(--text);margin-top:4px}
.signature{position:absolute;left:116px;top:440px;width:170px;height:60px;border-radius:6px;background:linear-gradient(90deg,#b4bec7,#c4ced6)}

/* Skills */
.skills{position:absolute;left:0;top:540px;width:1200px;height:470px;background:var(--white)}
.skill{position:absolute;width:390px}
.skill .row{display:flex;justify-content:space-between;font-size:15px;color:var(--ink)}
.skill .bar{margin-top:14px;height:4px;background:var(--track)}
.skill .bar i{display:block;height:4px;background:var(--ink)}

/* Education */
.education{position:absolute;left:0;top:1010px;width:1200px;height:570px;background:var(--paper)}
.timeline-line{position:absolute;left:598px;top:140px;width:3px;height:370px;background:var(--ink)}
.edu-label{position:absolute;font-family:"Montserrat",Arial,sans-serif;font-weight:600;font-size:20px;color:var(--ink)}
.edu-card{position:absolute;width:290px;padding:22px 24px;background:var(--white);border-radius:24px;font-size:12px;line-height:1.6;color:var(--muted)}
.edu-nav{position:absolute;left:567px;top:516px;width:66px;height:34px;border-radius:17px;background:var(--ink)}

/* Worked for */
.worked{position:absolute;left:0;top:1580px;width:1200px;height:600px;background:var(--white)}
.worked-panel{position:absolute;left:760px;top:0;width:440px;height:600px;background:var(--ink)}
.worked-title{position:absolute;left:112px;top:60px;font-family:"Montserrat",Arial,sans-serif;font-weight:600;font-size:30px;color:var(--ink)}
.worked-intro{position:absolute;left:112px;top:112px;width:420px;font-size:13px;line-height:1.6;color:var(--text)}
.client{position:absolute;left:112px;width:410px;height:70px;display:flex;align-items:center;border:1px solid var(--line);border-radius:4px;background:var(--white);color:var(--ink);font-size:15px}
.client .num{width:70px;height:100%;display:flex;align-items:center;justify-content:center;border-right:1px solid var(--line);font-family:"Montserrat",Arial,sans-serif;font-weight:500;font-size:14px;flex:none}
.client .label{padding:0 20px;line-height:1.35}
.client.active{background:var(--ink);color:var(--white);border-color:var(--ink)}
.client.active .num{border-right-color:#444}
.worked-photo{position:absolute;left:570px;top:160px;width:540px;height:330px;border-radius:8px;background:linear-gradient(135deg,#cfd6dc 0%,#8fa1b1 45%,#3f5366 100%)}

/* Other */
.other{position:absolute;left:0;top:2180px;width:1200px;height:410px;background:var(--paper)}
.gallery{position:absolute;left:112px;top:114px;display:flex}
.gallery div{width:245px;height:250px}
.g1{background:linear-gradient(160deg,#c6c1b5,#6b6658 60%,#3c3a33)}
.g2{background:linear-gradient(160deg,#d7d4cc,#8a877f 60%,#4e4c47)}
.g3{background:radial-gradient(circle at 45% 40%,#f2e8b8,#9a8a4a 45%,#3c4a2a 100%)}
.g4{background:linear-gradient(160deg,#8a1e22,#5c1014 60%,#2a0a0c)}

/* Footer */
.footer{position:absolute;left:0;top:2590px;width:1200px;height:98px;background:var(--ink);display:flex;align-items:center;justify-content:center;gap:10px;color:#cfcfcf;font-size:13px}
.footer .mark{width:14px;height:14px;border-radius:50%;background:#cfcfcf}
</style>
</head>
<body>

<header class="hero">
  <div class="hero-photo" role="img" aria-label="Portrait photo of Maarten, smiling, wearing glasses"></div>
  <div class="brand">VELMOT BV</div>
  <nav class="person-switch"><span class="off">Maarten</span><span class="on">Liesbeth</span></nav>
  <div class="toolbar">
    <svg width="24" height="18" viewBox="0 0 24 18" aria-label="Menu"><rect y="1" width="22" height="2.5" fill="#fff"/><rect y="8" width="22" height="2.5" fill="#fff"/><rect y="15" width="22" height="2.5" fill="#fff"/></svg>
    <span class="dot"></span><span class="dot"></span><span class="dot"></span>
  </div>

  <div class="name-label">Name</div>
  <div class="name">Maarten</div>

  <div class="jobs" style="left:112px">
    <h4>Annual jobs</h4>
    <div class="job"><b>Advisor Kestra</b><small>Harvelt Groep</small></div>
    <div class="job"><b>Advisor Flow &amp; known</b><small>Harvelt Groep</small></div>
  </div>
  <div class="jobs" style="left:384px">
    <h4>Finished jobs</h4>
    <div class="job"><b>Controller a.i. Kestra</b><small>Harvelt Groep</small></div>
    <div class="job"><b>Advisor Dunmore Green</b><small>Harvelt Groep</small></div>
    <div class="job"><b>Financial director Tolvane</b><small>Harvelt Groep</small></div>
  </div>

  <div class="signature" role="img" aria-label="Handwritten signature of Maarten"></div>
</header>

<section class="skills">
  <h2 class="section-title" style="top:62px">My Skills</h2>
  <div class="skill" style="left:150px;top:150px"><div class="row"><span>Annual reporting</span><span>40%</span></div><div class="bar"><i style="width:40%"></i></div></div>
  <div class="skill" style="left:640px;top:150px"><div class="row"><span>Financial monthly reporting</span><span>35%</span></div><div class="bar"><i style="width:35%"></i></div></div>
  <div class="skill" style="left:150px;top:230px"><div class="row"><span>Accounting</span><span>100%</span></div><div class="bar"><i style="width:100%"></i></div></div>
  <div class="skill" style="left:640px;top:230px"><div class="row"><span>Financial management</span><span>40%</span></div><div class="bar"><i style="width:40%"></i></div></div>
  <div class="skill" style="left:150px;top:310px"><div class="row"><span>Project management</span><span>35%</span></div><div class="bar"><i style="width:35%"></i></div></div>
  <div class="skill" style="left:640px;top:310px"><div class="row"><span>Team player</span><span>35%</span></div><div class="bar"><i style="width:35%"></i></div></div>
  <div class="skill" style="left:150px;top:390px"><div class="row"><span>Trouble shooter</span><span>40%</span></div><div class="bar"><i style="width:40%"></i></div></div>
  <div class="skill" style="left:640px;top:390px"><div class="row"><span>ETC.</span><span>40%</span></div><div class="bar"><i style="width:40%"></i></div></div>
</section>

<section class="education">
  <h2 class="section-title" style="top:62px">Education</h2>
  <div class="timeline-line"></div>
  <div class="edu-label" style="left:456px;top:158px">Orvan (RA)</div>
  <div class="edu-card" style="left:740px;top:150px">We never stop learning: audits, reporting standards and tax law were studied in depth, with a strong focus on practical accounting for small firms.</div>
  <div class="edu-card" style="left:165px;top:330px">Secondary school with economics, mathematics and languages laid the foundation for a long career in finance, control and interim management roles.</div>
  <div class="edu-label" style="left:645px;top:346px">Atheneum B</div>
  <div class="edu-nav">
    <svg width="66" height="34" viewBox="0 0 66 34" aria-label="Previous and next"><path d="M28 12l-5 5 5 5" stroke="#fff" stroke-width="2" fill="none"/><path d="M38 12l5 5-5 5" stroke="#fff" stroke-width="2" fill="none"/></svg>
  </div>
</section>

<section class="worked">
  <div class="worked-panel"></div>
  <h2 class="worked-title">Worked for</h2>
  <p class="worked-intro">Over the years we supported firms in legal, audit and energy sectors, from quick interim fixes to long board roles and lasting client relations.</p>
  <div class="client" style="top:210px"><span class="num">01</span><span class="label">Brask Advocaten&amp;Notarissen</span></div>
  <div class="client active" style="top:290px"><span class="num">02</span><span class="label">Norvale</span></div>
  <div class="client" style="top:370px;height:80px"><span class="num">03</span><span class="label">On the other hand, we denounce<br>with righteous indignation</span></div>
  <div class="worked-photo" role="img" aria-label="Laptop showing a photo of a business meeting"></div>
</section>

<section class="other">
  <h2 class="section-title" style="top:70px">Other</h2>
  <div class="gallery">
    <div class="g1" role="img" aria-label="Photo of a person using a video camera"></div>
    <div class="g2" role="img" aria-label="Photo of a street scene in black and white"></div>
    <div class="g3" role="img" aria-label="Photo of sunlight through a forest"></div>
    <div class="g4" role="img" aria-label="Photo of red roses"></div>
  </div>
</section>

<footer class="footer"><span class="mark"></span><span>© 2015 www.pruxelo-example.com</span></footer>

</body>
</html>
```